Label Design for Food Brand

We want a modern label for our spice blends. We are completely open in which direction, it should be modern and beautiful.

Use for Sample spice mixture: "Kelvo Dusk"

Here the Packaging:
https://www.merlitrove-example.com/media/xlarge/1700_1.jpg
Abmessung: Ø 54 x 67 mm

Target Market(s)

Food

Industry/Entity Type

Food

Requirements
Must have
• Logo, Name of Savrona
Should not have
• Images of food

```html
<!DOCTYPE html>
<html lang="en">
<head>
<meta charset="utf-8">
<title>Savrona – Kelvo Dusk Spice Mixture Label</title>
<link href="https://fonts.googleapis.com/css2?family=Bebas+Neue&family=Open+Sans:wght@700&display=swap" rel="stylesheet">
<style>
  :root {
    --page: #ffffff;
    --label-black: #000000;
    --brand-red: #a60000;
    --ink-white: #ffffff;
  }
  html, body {
    margin: 0;
    padding: 0;
    width: 1200px;
    height: 915px;
    overflow: hidden;
    background: var(--page);
  }
  .canvas {
    position: relative;
    width: 1200px;
    height: 915px;
  }
  .label {
    position: absolute;
    left: 221px;
    top: 153px;
    width: 743px;
    height: 597px;
    border-radius: 28px;
    background: var(--label-black);
    overflow: hidden;
  }
  .label__band {
    position: absolute;
    left: 0;
    width: 100%;
  }
  .label__band--top { top: 0; height: 80px; }
  .label__band--bottom { bottom: 0; height: 80px; }
  .brand-name {
    position: absolute;
    left: 0;
    right: 0;
    top: 148px;
    margin: 0;
    text-align: center;
    font-family: "Open Sans", sans-serif;
    font-weight: 700;
    font-size: 72px;
    line-height: 1;
    letter-spacing: 1px;
    color: var(--ink-white);
  }
  .ribbon {
    position: absolute;
    left: 63px;
    top: 267px;
    width: 618px;
    height: 148px;
  }
  .product-name {
    position: absolute;
    left: 0;
    right: 0;
    top: 300px;
    margin: 0;
    text-align: center;
    font-family: "Bebas Neue", sans-serif;
    font-weight: 400;
    font-size: 112px;
    line-height: 1;
    letter-spacing: 5px;
    color: var(--ink-white);
  }
  .product-type {
    position: absolute;
    left: 0;
    right: 0;
    top: 430px;
    margin: 0;
    text-align: center;
    font-family: "Bebas Neue", sans-serif;
    font-weight: 400;
    font-size: 72px;
    line-height: 1;
    letter-spacing: 3px;
    color: var(--ink-white);
  }
</style>
</head>
<body>
<main class="canvas">
  <section class="label">
    <svg class="label__band label__band--top" viewBox="0 0 743 80" preserveAspectRatio="none" role="img" aria-label="Red brush stroke band">
      <polygon points="0,0 743,0 743,60 600,72 420,50 250,46 120,40 0,38" fill="var(--brand-red)"/>
    </svg>

    <h1 class="brand-name">SAVRONA</h1>

    <svg class="ribbon" viewBox="0 0 618 148" aria-hidden="true">
      <polygon points="10,0 618,4 556,76 610,144 0,146 74,78" fill="var(--brand-red)"/>
      <polyline points="24,10 600,14 545,76 596,136 16,136 84,78 24,10"
        fill="none" stroke="var(--ink-white)" stroke-width="2.2" stroke-dasharray="7 5"/>
    </svg>

    <h2 class="product-name">Kelvo Dusk</h2>
    <p class="product-type">Spice Mixture</p>

    <svg class="label__band label__band--bottom" viewBox="0 0 743 80" preserveAspectRatio="none" role="img" aria-label="Red brush stroke band">
      <polygon points="0,46 130,52 300,40 470,26 600,20 743,16 743,80 0,80" fill="var(--brand-red)"/>
    </svg>
  </section>
</main>
</body>
</html>
```